Business Card for a New Zealand IT Startup

I need a business card for VELTA Holdings. We are a young startup based in New Zealand working in internet marketing and web development. The design should have some element connected to New Zealand, such as wave, koru or silver fern, just don't use a kiwi bird.

```html
<!DOCTYPE html>
<html lang="en">
<head>
<meta charset="utf-8">
<title>VELTA Holdings – Business Card</title>
<link rel="stylesheet" href="https://fonts.googleapis.com/css2?family=Jost:wght@400;500;600;700&display=swap">
<style>
  :root {
    --stage: #ececec;
    --card-white: #ffffff;
    --brand-blue: #0a6fbf;
    --brand-orange: #f15a24;
    --text-grey: #4d4d4d;
    --faint-blue: #e3eef8;
    --wave-light: rgba(255, 255, 255, 0.22);
  }
  * { box-sizing: border-box; margin: 0; padding: 0; }
  html, body {
    width: 1125px; height: 1200px; overflow: hidden;
    background: var(--stage);
    font-family: "Jost", "Futura", sans-serif;
  }
  .canvas { position: relative; width: 1125px; height: 1200px; }

  /* Front of card */
  .card-front {
    position: absolute; left: 150px; top: 98px;
    width: 825px; height: 471px;
    background: var(--card-white);
    overflow: hidden;
  }
  .edge-stripe { position: absolute; left: 0; top: 0; width: 13px; height: 471px; }
  .ocean-waves {
    position: absolute; left: 0; top: 0;
    width: 825px; height: 471px;
  }
  .brand-name {
    position: absolute; left: 49px; top: 42px;
    color: var(--brand-blue); font-weight: 600; line-height: 1;
  }
  .brand-name .word-main { display: block; font-size: 96px; letter-spacing: 2px; }
  .brand-name .word-sub { display: block; font-size: 28px; letter-spacing: 19px; margin-top: 6px; }
  .address {
    position: absolute; left: 49px; top: 233px;
    color: var(--text-grey); font-size: 20px; line-height: 25px;
  }
  .contact-list {
    position: absolute; left: 49px; top: 295px;
    list-style: none; color: var(--text-grey); font-size: 20px;
  }
  .contact-list li { display: flex; align-items: center; height: 26.5px; }
  .contact-list svg { width: 18px; height: 18px; margin-right: 14px; fill: var(--brand-blue); }
  .person {
    position: absolute; right: 48px; top: 292px; text-align: right;
  }
  .person-name { color: var(--brand-blue); font-size: 31px; font-weight: 600; line-height: 1.1; }
  .person-title { color: var(--brand-orange); font-size: 21px; font-weight: 400; }

  /* Back of card */
  .card-back {
    position: absolute; left: 150px; top: 631px;
    width: 825px; height: 470px;
    background: var(--brand-orange);
    border-radius: 30px;
    overflow: hidden;
    color: var(--card-white);
  }
  .back-waves { position: absolute; left: 0; bottom: 0; width: 825px; height: 470px; }
  .back-brand {
    position: absolute; left: 0; right: 0; top: 178px;
    display: flex; justify-content: center; align-items: center; gap: 20px;
    font-size: 56px; font-weight: 600; color: var(--card-white);
  }
  .back-brand .dot { width: 30px; height: 30px; border-radius: 50%; background: var(--card-white); }
  .back-web {
    position: absolute; left: 0; right: 0; top: 382px;
    text-align: center; font-size: 18px; letter-spacing: 9px;
  }
</style>
</head>
<body>
<main class="canvas">
  <section class="card-front">
    <svg class="ocean-waves" viewBox="0 0 825 471" aria-hidden="true">
      <path d="M420 471 C480 400 540 400 600 430 S720 470 825 380 V471 Z" fill="var(--faint-blue)"/>
      <path d="M470 360 C540 300 610 320 660 350 S760 370 825 290" fill="none" stroke="var(--faint-blue)" stroke-width="26" stroke-linecap="round"/>
      <path d="M520 250 C590 190 650 215 700 240 S780 250 825 190" fill="none" stroke="var(--faint-blue)" stroke-width="18" stroke-linecap="round"/>
      <path d="M580 150 C640 100 690 120 730 140 S800 145 825 110" fill="none" stroke="var(--faint-blue)" stroke-width="12" stroke-linecap="round"/>
    </svg>
    <svg class="edge-stripe" viewBox="0 0 13 471" preserveAspectRatio="none">
      <polygon points="0,0 13,0 13,196 0,208" fill="var(--brand-orange)"/>
      <polygon points="0,208 13,196 13,471 0,471" fill="var(--brand-blue)"/>
    </svg>
    <div class="brand-name">
      <span class="word-main">VELTA</span>
      <span class="word-sub">HOLDINGS</span>
    </div>
    <p class="address">14 Harbour View Road<br>Wellington, NZ 6011</p>
    <ul class="contact-list">
      <li><svg viewBox="0 0 24 24"><path d="M6.6 10.8a15 15 0 0 0 6.6 6.6l2.2-2.2c.3-.3.7-.4 1-.2 1.1.4 2.3.6 3.6.6.6 0 1 .4 1 1V20c0 .6-.4 1-1 1A17 17 0 0 1 3 4c0-.6.4-1 1-1h3.5c.6 0 1 .4 1 1 0 1.3.2 2.5.6 3.6.1.3 0 .7-.2 1z"/></svg>021 555 0147</li>
      <li><svg viewBox="0 0 24 24"><path d="M7 1h10a2 2 0 0 1 2 2v18a2 2 0 0 1-2 2H7a2 2 0 0 1-2-2V3a2 2 0 0 1 2-2zm0 3v14h10V4zm5 15.5a1 1 0 1 0 0 2 1 1 0 0 0 0-2z"/></svg>022 555 0183</li>
      <li><svg viewBox="0 0 24 24"><path d="M6 2h12v6H6zM3 9h18a2 2 0 0 1 2 2v7h-4v4H5v-4H1v-7a2 2 0 0 1 2-2zm4 8v3h10v-3z"/></svg>04 555 0192</li>
      <li><svg viewBox="0 0 24 24"><path d="M2 5h20v14H2zm2 2v.5l8 5.5 8-5.5V7zm0 3v7h16v-7l-8 5.5z"/></svg>mara@veltaholdings.com</li>
      <li><svg viewBox="0 0 24 24"><circle cx="12" cy="12" r="10"/><path d="M8 6c2 1 2 3 1 4s-3 1-2 3 3 1 3 3-1 3 0 4M15 4c-1 2 0 3 2 3s3 2 1 4-1 4 1 5" stroke="#fff" stroke-width="1.6" fill="none"/></svg>www.veltaholdings.com</li>
    </ul>
    <div class="person">
      <p class="person-name">MARA TANE</p>
      <p class="person-title">CEO/FOUNDER</p>
    </div>
  </section>

  <section class="card-back">
    <svg class="back-waves" viewBox="0 0 825 470" aria-hidden="true">
      <path d="M0 420 C120 380 220 380 330 410 S560 450 825 390" fill="none" stroke="var(--wave-light)" stroke-width="10" stroke-linecap="round"/>
      <path d="M0 80 C140 40 260 50 380 70 S620 90 825 40" fill="none" stroke="var(--wave-light)" stroke-width="6" stroke-linecap="round"/>
    </svg>
    <div class="back-brand"><span class="dot"></span><span>VELTA Holdings</span></div>
    <p class="back-web">www.veltaholdings.com</p>
  </section>
</main>
</body>
</html>
```